Velvet Riot Rising Line of Sparkling Wine & Spirits

Back info: Nora Beth Quill Owner 555-318-4402 1480 E. Harlow Ave, Bldg. 2, & 3, Calder Ca. 95871
Sparkling Wines & Memorabilia www.velvetriotrising.com
Ok I have uploaded the winning design. The color that I am after is the Fushia, Raspberry, Red, Matte Satin Matalic Finish. With a 24 Karet Gold color Foil. The Bottle is on the top row and it's the 2nd Bottle in. That is the Color that I want. This is the style of font. Make sure that you put what we're advertising. Good Luck to you all. Warmest regards, Nora
21 & up UniSex
Sparkling Wine and Memorabilia
there listed up above.....

```html
<!DOCTYPE html>
<html lang="en">
<head>
<meta charset="utf-8">
<title>Velvet Riot Rising – Business Card</title>
<link rel="stylesheet" href="https://fonts.googleapis.com/css2?family=Cinzel:wght@400;700&display=swap">
<style>
  :root {
    --backdrop: #38383b;
    --raspberry: #8f0d4b;
    --raspberry-light: #9e1d58;
    --gold: #d4a63a;
    --gold-deep: #a8781c;
    --ivory: #f6eef2;
  }
  * { margin: 0; padding: 0; box-sizing: border-box; }
  html, body {
    width: 1200px; height: 1200px; overflow: hidden;
    background: var(--backdrop);
  }
  .canvas {
    position: relative; width: 1200px; height: 1200px;
    display: flex; flex-direction: column; align-items: center; justify-content: center; gap: 52px;
  }
  .card {
    position: relative; width: 900px; height: 514px;
    border-radius: 38px; overflow: hidden;
    background: linear-gradient(115deg, var(--raspberry) 0%, var(--raspberry-light) 50%, var(--raspberry) 100%);
    box-shadow: 0 18px 40px rgba(0,0,0,.45);
    font-family: 'Cinzel', serif;
  }
  .card-front .gold-edge {
    position: absolute; left: 0; right: 0; bottom: 0; height: 16px;
    background: linear-gradient(90deg, var(--gold-deep), var(--gold) 45%, #f0d27a 60%, var(--gold-deep));
  }
  .contact {
    position: absolute; left: 64px; top: 150px;
  }
  .contact .name {
    color: var(--gold); font-size: 44px; font-weight: 400; letter-spacing: 1px; line-height: 1;
  }
  .contact .role {
    color: var(--ivory); font-size: 28px; margin-top: 6px; margin-bottom: 26px;
  }
  .contact .row {
    display: flex; align-items: flex-start; gap: 14px;
    color: var(--ivory); font-size: 22px; line-height: 1.25; margin-bottom: 8px;
  }
  .contact .row svg { flex: none; width: 24px; height: 24px; margin-top: 2px; }
  .contact .row .lines { display: flex; flex-direction: column; }
  .brand-name {
    position: absolute; color: var(--gold); font-family: 'Cinzel', serif; font-weight: 700;
    text-align: center; line-height: 1.05;
  }
  .card-front .brand-name { right: 70px; top: 150px; width: 300px; font-size: 44px; }
  .card-back .brand-name {
    left: 0; right: 0; top: 50%; transform: translateY(-50%); font-size: 76px;
  }
</style>
</head>
<body>
<main class="canvas">
  <section class="card card-front">
    <div class="contact">
      <h1 class="name">Nora Beth Quill</h1>
      <p class="role">Owner</p>
      <div class="row">
        <svg viewBox="0 0 24 24" aria-hidden="true"><path fill="var(--gold)" d="M6.6 10.8a15 15 0 0 0 6.6 6.6l2.2-2.2a1 1 0 0 1 1-.25 11.4 11.4 0 0 0 3.6.57 1 1 0 0 1 1 1V20a1 1 0 0 1-1 1A17 17 0 0 1 3 4a1 1 0 0 1 1-1h3.5a1 1 0 0 1 1 1 11.4 11.4 0 0 0 .57 3.6 1 1 0 0 1-.25 1z"/></svg>
        <span>555-318-4402 1480</span>
      </div>
      <div class="row">
        <svg viewBox="0 0 24 24" aria-hidden="true" fill="none" stroke="var(--gold)" stroke-width="1.8"><circle cx="12" cy="12" r="9.5"/><ellipse cx="12" cy="12" rx="4.2" ry="9.5"/><path d="M2.5 12h19M4 7h16M4 17h16"/></svg>
        <span>www.velvetriotrising.com</span>
      </div>
      <div class="row">
        <svg viewBox="0 0 24 24" aria-hidden="true"><path fill="var(--gold)" d="M12 2a7 7 0 0 0-7 7c0 5.2 7 13 7 13s7-7.8 7-13a7 7 0 0 0-7-7zm0 9.6A2.6 2.6 0 1 1 12 6.4a2.6 2.6 0 0 1 0 5.2z"/></svg>
        <span class="lines">
          <span>E. Harlow Ave, Bldg. 2, &amp; 3,</span>
          <span>Calder Ca. 95871</span>
          <span>Sparkling Wines &amp; Memorabilia</span>
        </span>
      </div>
    </div>
    <p class="brand-name">Velvet Riot Rising</p>
    <div class="gold-edge"></div>
  </section>

  <section class="card card-back">
    <p class="brand-name">Velvet Riot Rising</p>
  </section>
</main>
</body>
</html>
```